CoinHarbor.com Site Redesign

We are looking to redesign our CoinHarbor.com site. This site is focused on helping consumers make smart financial decisions. We provide reviews and articles in various categories.

We are looking for a responsive design to run on wordpress. We will also have adsense advertisements on our page and will want some ad spot space. We are thinking of two column design vs. single column.

Here is an example of what our competitors look like:
ShopperBeacon.org (mostly reviews vs. articles)
Homepage - https://www.shopperbeacon.example/
Category Review Listing - https://www.shopperbeacon.example/mortgage-refinance/best-mortgage-refinance
Individual Review - https://www.shopperbeacon.example/mortgage-refinance/c/loan-orchard-mortgage-refinance-review

- I like that the site is extremely clean. I like the fixed header in mobile

PilotGuide
Homepage - https://www.pilotguide.example/
Category Review Listing-https://www.pilotguide.example/auto_insurance/index.php
Individual Review- https://www.pilotguide.example/auto_insurance/drivora_review.php

Articles - https://www.pilotguide.example/blog/2017/11/20/going-on-a-holiday-road-trip-be-prepared-for-these-hazards/

What I Like? I like the two column layout in that it gives room for advertising.
What I Do NOT Like? The top navigation is a little cumbersome and old. Mobile view is not very good. Content seems a bit cluttered.

PennyMoth
Homepage - https://www.pennymoth.example
Category Review Listing - https://www.pennymoth.example/blog/insurance/best-car-insurance-companies/?trk=pm_gn1_4.0
Individual Review- https://www.pennymoth.example/blog/insurance/veloro-insurance-review/

What I Like? very clean. Like the use of white space and focus on bright color call to action buttons.
What I Do NOT Like? In mobile a lot of content is pushed below the fold because of the large image above the fold. Reviews are not well organized.

Target Market(s)

consumers interested in saving money and making smart financial decisions

Industry/Entity Type

Financial

Logo Text

CoinHarbor.com or CoinHarbor

Coding

Coded - Design and coding required

Number of Pages Required

5+ page

Font styles to use
Sans Serif

Colors

Designer to choose colors to be used in the design.

Requirements
Must have
• -responsive design
• -room for ad space in the right column
Nice to have
• -good use of white space
• -clean layouts
Should not have
• -clutter

```html
<!DOCTYPE html>
<html lang="en">
<head>
<meta charset="utf-8">
<title>CoinHarbor.com – Make smarter financial decisions</title>
<link href="https://fonts.googleapis.com/css2?family=Lato:wght@400;700;900&display=swap" rel="stylesheet">
<style>
:root{
  --blue:#1f7bc8;
  --blue-deep:#1466c2;
  --blue-bright:#2b8fe0;
  --hero-a:#1d5fd6;
  --hero-b:#2f7df0;
  --band:#1d79c0;
  --ink:#2a2a2a;
  --text:#4a4a4a;
  --muted:#6b6b6b;
  --nav:#262626;
  --bottom:#2f2f2f;
  --soft:#f3f4f6;
  --line:#d9dde2;
  --white:#ffffff;
}
*{box-sizing:border-box;margin:0;padding:0}
html,body{width:1200px;height:2826px;overflow:hidden}
body{font-family:'Lato',sans-serif;color:var(--text);background:var(--white);position:relative}
a{color:inherit;text-decoration:none}

/* header */
.topbar{height:64px;position:relative}
.brand{position:absolute;left:75px;top:18px;display:flex;align-items:center;gap:10px;font-size:25px;font-weight:900;color:var(--blue-deep);letter-spacing:-.3px}
.brand-mark{width:26px;height:26px;background:var(--blue-deep)}
.tagline{position:absolute;left:440px;top:24px;font-size:14px;font-weight:700;color:var(--ink)}
.search{position:absolute;left:883px;top:15px;width:242px;height:34px;border:1px solid var(--line);border-radius:17px;background:#f5f6f8;display:flex;align-items:center;padding:0 14px;font-size:13px;color:var(--ink);justify-content:space-between}
.mainnav{height:55px;background:var(--nav);display:flex;align-items:center;padding:0 75px;position:relative}
.mainnav a{color:var(--white);font-size:13px;font-weight:700;letter-spacing:.3px;margin-right:44px}
.auth{position:absolute;right:75px;top:11px;display:flex;gap:8px}
.btn{height:34px;border-radius:17px;font-size:13px;font-weight:700;color:var(--white);display:flex;align-items:center;justify-content:center;letter-spacing:.3px}
.btn-login{width:98px;border:1.5px solid var(--white)}
.btn-signup{width:98px;background:var(--blue-bright)}

/* hero */
.hero{height:386px;position:relative;color:var(--white);text-align:center}
.hero-bg{position:absolute;inset:0;background:linear-gradient(100deg,var(--hero-a) 0%,#1a4fb8 45%,var(--hero-b) 100%)}
.hero-inner{position:relative;padding-top:90px}
.hero h1{font-size:50px;font-weight:900;letter-spacing:-.3px;line-height:1}
.hero .sub{font-size:20px;font-weight:900;margin-top:12px;letter-spacing:.3px}
.finder{margin:26px auto 0;width:567px;height:50px;background:var(--white);border-radius:25px;display:flex;align-items:center;justify-content:center;font-size:26px;font-weight:900;color:var(--ink)}
.finder span{color:#8a8a8a;font-weight:700;margin-left:8px}
.disclosure{font-size:13px;font-weight:700;margin-top:24px}
.disclosure a{color:#8fd0ff;text-decoration:underline;font-weight:400}

/* about */
.about{height:368px;background:linear-gradient(#ffffff,var(--soft));text-align:center;padding-top:42px}
.about h2{font-size:29px;font-weight:700;color:var(--ink)}
.about .kicker{font-size:16px;font-weight:700;color:var(--blue);margin-top:8px}
.pillars{display:flex;justify-content:center;gap:0;margin-top:33px}
.pillar{width:359px}
.pillar-icon{width:90px;height:90px;border:2px solid var(--blue);border-radius:50%;margin:0 auto;display:flex;align-items:center;justify-content:center}
.pillar h3{font-size:19px;font-weight:700;color:var(--blue);margin-top:22px}
.pillar p{font-size:15.5px;line-height:1.6;margin:6px auto 0;width:300px;color:var(--text)}

/* categories */
.categories{height:849px;position:relative}
.tiles{position:absolute;left:75px;top:54px;display:grid;grid-template-columns:repeat(3,245px);grid-auto-rows:176px;column-gap:13px;row-gap:14px}
.tile{position:relative;display:flex;align-items:center;justify-content:center;overflow:hidden}
.tile-photo{position:absolute;inset:0}
.tile-name{position:relative;color:var(--white);font-size:23px;font-weight:900;text-align:center;line-height:1.1;text-shadow:0 1px 4px rgba(0,0,0,.5)}
.t1 .tile-photo{background:linear-gradient(135deg,#6d6258,#a49a90)}
.t2 .tile-photo{background:linear-gradient(135deg,#8a8078,#c4bcb4)}
.t3 .tile-photo{background:linear-gradient(135deg,#3a4a3a,#8a9688)}
.t4 .tile-photo{background:linear-gradient(135deg,#4a3e4e,#9a6c5c)}
.t5 .tile-photo{background:linear-gradient(135deg,#4b352c,#8d6c58)}
.t6 .tile-photo{background:linear-gradient(135deg,#1e2630,#4c5966)}
.t7 .tile-photo{background:linear-gradient(135deg,#2e2c2c,#6a6462)}
.t8 .tile-photo{background:linear-gradient(135deg,#7e6a5a,#b9a38c)}
.t9 .tile-photo{background:linear-gradient(135deg,#3e3a38,#7a6e66)}
.t10 .tile-photo{background:linear-gradient(135deg,#4a4642,#8c8884)}
.t11 .tile-photo{background:linear-gradient(135deg,#6a625c,#a89e94)}
.t12 .tile-photo{background:linear-gradient(135deg,#2c2624,#6c5a4c)}
.ads{position:absolute;left:855px;top:54px;width:272px;display:flex;flex-direction:column;gap:19px}
.ad{width:272px;height:226px}
.ad-1{background:linear-gradient(#c9a98c,#6e6058 60%,#1e5ba8 82%)}
.ad-2{background:linear-gradient(#7ab826 0 32%,#243040 32%)}
.ad-3{background:linear-gradient(#1a5fb0 0 88%,#2e8a3a 88%)}

/* articles */
.articles{height:500px;background:var(--soft);position:relative}
.articles h2{position:absolute;left:75px;top:40px;font-size:27px;font-weight:700;color:var(--ink)}
.pager{position:absolute;right:75px;top:46px;display:flex;gap:12px}
.cards{position:absolute;left:75px;top:98px;display:flex;gap:29px}
.card{width:331px}
.card-photo{height:185px}
.p1{background:linear-gradient(135deg,#b9c0a8,#7d8a6e)}
.p2{background:linear-gradient(135deg,#3b5a2a,#6d8f3c 55%,#2c2c2c)}
.p3{background:linear-gradient(135deg,#e6e6e6,#c9c9c9)}
.card h3{font-size:21px;font-weight:700;color:var(--blue);line-height:1.2;margin-top:16px}
.card p{font-size:14.5px;line-height:1.7;margin-top:8px;color:var(--text)}
.card p a{color:var(--blue);font-weight:700}

/* subscribe */
.subscribe{height:211px;background:var(--band);color:var(--white);text-align:center;padding-top:32px}
.subscribe h2{font-size:29px;font-weight:700}
.subscribe p{font-size:16px;margin-top:10px;color:#e4f1fb}
.signup-field{margin:24px auto 0;width:450px;height:44px;background:var(--white);border-radius:22px;display:flex;align-items:center;justify-content:space-between;padding:0 4px 0 20px;color:var(--ink);font-size:13px}
.go{width:38px;height:38px;border-radius:50%;background:#163e8a;color:var(--white);font-weight:900;font-size:15px;display:flex;align-items:center;justify-content:center}

/* footer */
.sitefoot{height:313px;position:relative}
.fcol{position:absolute;top:38px}
.fcol h4{font-size:16px;font-weight:700;color:var(--blue-deep);margin-bottom:10px}
.fcol ul{list-style:none}
.fcol li{font-size:13.5px;line-height:28.5px;color:var(--text)}
.fcol.services ul{display:grid;grid-template-columns:178px auto;grid-auto-flow:column;grid-template-rows:repeat(8,28.5px)}
.fcol.disclaim p{font-size:13.5px;line-height:1.78;width:340px;color:var(--text)}
.follow{margin-top:18px}
.follow h4{margin-bottom:8px}
.social{display:flex;gap:14px;font-size:13px;font-weight:700;color:#444}
.bottombar{height:80px;background:var(--bottom);color:#bdbdbd;font-size:12px;display:flex;align-items:center;justify-content:space-between;padding:0 75px}
</style>
</head>
<body>

<header>
  <div class="topbar">
    <a class="brand" href="#"><span class="brand-mark"></span>CoinHarbor.com</a>
    <div class="tagline">Trusted Financial Advice and Reviews Since 2001</div>
    <div class="search">Search..
      <svg width="14" height="14" viewBox="0 0 14 14"><circle cx="6" cy="6" r="4.3" fill="none" stroke="#1466c2" stroke-width="2"/><line x1="9.2" y1="9.2" x2="13" y2="13" stroke="#1466c2" stroke-width="2.2"/></svg>
    </div>
  </div>
  <nav class="mainnav">
    <a href="#">ANNUITIES</a><a href="#">AUTO INSURANCE</a><a href="#">CREDIT MONITORING</a><a href="#">DEBT MANAGEMENT</a><a href="#">MORTGAGES</a>
    <div class="auth"><a class="btn btn-login" href="#">LOG IN</a><a class="btn btn-signup" href="#">SIGN UP</a></div>
  </nav>
</header>

<section class="hero">
  <div class="hero-bg" role="img" aria-label="Photo of a smiling couple reviewing finances at a laptop, tinted blue"></div>
  <div class="hero-inner">
    <h1>Make smarter financial decisions</h1>
    <div class="sub">FIND THE BEST FINANCIAL PRODUCTS &amp; SERVICES</div>
    <div class="finder">I'm looking for<span>product and category</span></div>
    <div class="disclosure">Disclosure: We receive advertising revenue from some partners. <a href="#">Learn more.</a></div>
  </div>
</section>

<section class="about">
  <h2>What is CoinHarbor.com?</h2>
  <div class="kicker">Financial Service Advice and Reviews</div>
  <div class="pillars">
    <div class="pillar">
      <div class="pillar-icon"><svg width="40" height="36" viewBox="0 0 40 36"><rect x="1" y="1" width="38" height="34" fill="none" stroke="#1f7bc8" stroke-width="2.5"/><rect x="8" y="18" width="4" height="12" fill="#1f7bc8"/><rect x="15" y="10" width="4" height="20" fill="#1f7bc8"/><rect x="22" y="14" width="4" height="16" fill="#1f7bc8"/><rect x="29" y="7" width="4" height="23" fill="#1f7bc8"/></svg></div>
      <h3>We Analyze &amp; Explain</h3>
      <p>We analyze &amp; explain how each online service works.</p>
    </div>
    <div class="pillar">
      <div class="pillar-icon"><svg width="30" height="38" viewBox="0 0 30 38"><path d="M0 0H20L30 10V38H0Z" fill="#1f7bc8"/><path d="M20 0V10H30" fill="#9cc8ec"/><rect x="6" y="16" width="18" height="2.5" fill="#fff"/><rect x="6" y="22" width="18" height="2.5" fill="#fff"/><rect x="6" y="28" width="12" height="2.5" fill="#fff"/></svg></div>
      <h3>We Test &amp; Compare</h3>
      <p>We test &amp; compare the leading services in each category</p>
    </div>
    <div class="pillar">
      <div class="pillar-icon"><svg width="34" height="34" viewBox="0 0 34 34"><rect x="0" y="14" width="8" height="20" fill="#1f7bc8"/><path d="M11 14L18 2C21 1 23 3 22 7L20 12H31C33 12 34 14 33 16L29 31C28.5 33 27 34 25 34H11Z" fill="#1f7bc8"/></svg></div>
      <h3>We Review &amp; Rate</h3>
      <p>We review and rate each service to show which is best</p>
    </div>
  </div>
</section>

<section class="categories">
  <div class="tiles">
    <a class="tile t1" href="#"><div class="tile-photo" role="img" aria-label="Photo of coins being dropped into a jar"></div><span class="tile-name">Annuities</span></a>
    <a class="tile t2" href="#"><div class="tile-photo" role="img" aria-label="Photo of hands sheltering a toy car"></div><span class="tile-name">Auto Insurance</span></a>
    <a class="tile t3" href="#"><div class="tile-photo" role="img" aria-label="Photo of a credit score shown on devices"></div><span class="tile-name">Credit Monitoring</span></a>
    <a class="tile t4" href="#"><div class="tile-photo" role="img" aria-label="Photo of credit cards with a repair note"></div><span class="tile-name">Credit Repair</span></a>
    <a class="tile t5" href="#"><div class="tile-photo" role="img" aria-label="Photo of bills and a calculator on a desk"></div><span class="tile-name">Debt Management</span></a>
    <a class="tile t6" href="#"><div class="tile-photo" role="img" aria-label="Photo of a hooded figure at a laptop"></div><span class="tile-name">Identity Theft</span></a>
    <a class="tile t7" href="#"><div class="tile-photo" role="img" aria-label="Photo of a businessman holding an umbrella"></div><span class="tile-name">Life Insurance</span></a>
    <a class="tile t8" href="#"><div class="tile-photo" role="img" aria-label="Photo of a mortgage application form with keys"></div><span class="tile-name">Mortgages</span></a>
    <a class="tile t9" href="#"><div class="tile-photo" role="img" aria-label="Photo of a trader in front of market charts"></div><span class="tile-name">Online Brokerages</span></a>
    <a class="tile t10" href="#"><div class="tile-photo" role="img" aria-label="Photo of a payday loan form and calculator"></div><span class="tile-name">Payday Loans</span></a>
    <a class="tile t11" href="#"><div class="tile-photo" role="img" aria-label="Photo of a person reviewing personal finances"></div><span class="tile-name">Personal Finance</span></a>
    <a class="tile t12" href="#"><div class="tile-photo" role="img" aria-label="Photo of a student with a stack of books"></div><span class="tile-name">Student Loan<br>Consolidation</span></a>
  </div>
  <aside class="ads">
    <div class="ad ad-1" role="img" aria-label="Advertisement: hybrid sedan promotion"></div>
    <div class="ad ad-2" role="img" aria-label="Advertisement: clean fleet trade event"></div>
    <div class="ad ad-3" role="img" aria-label="Advertisement: earthquake drill campaign"></div>
  </aside>
</section>

<section class="articles">
  <h2>Recent Articles</h2>
  <div class="pager">
    <svg width="12" height="18" viewBox="0 0 12 18"><path d="M10 2L3 9L10 16" fill="none" stroke="#2a2a2a" stroke-width="2.5"/></svg>
    <svg width="12" height="18" viewBox="0 0 12 18"><path d="M2 2L9 9L2 16" fill="none" stroke="#2a2a2a" stroke-width="2.5"/></svg>
  </div>
  <div class="cards">
    <article class="card">
      <div class="card-photo p1" role="img" aria-label="Photo of a roll of dollar bills"></div>
      <h3>5 “Easy” Ways Parents Can Save $1000’s a Year</h3>
      <p>Parents, let’s face it – the high cost of raising children leaves us all needing a little extra money. Short of getting a big raise, switching jobs, or winning... <a href="#">Read More</a></p>
    </article>
    <article class="card">
      <div class="card-photo p2" role="img" aria-label="Photo of a couple riding a motorcycle"></div>
      <h3>Motorcycle Insurance Basics</h3>
      <p>Motorcycle insurance can be quite expensive; it can be the same amount as an auto insurance quote in some cases. Depending on the coverage you select and your driving... <a href="#">Read More</a></p>
    </article>
    <article class="card">
      <div class="card-photo p3" role="img" aria-label="Photo of an auto insurance policy with car keys"></div>
      <h3>How Do I Get Cheap Auto Insurance?</h3>
      <p>If you’re looking for cheap auto insurance, then you aren’t alone. Many drivers regularly search for lower cost, more affordable insurance for their vehicles on a regular basis. If..... <a href="#">Read More</a></p>
    </article>
  </div>
</section>

<section class="subscribe">
  <h2>Email Subscribe</h2>
  <p>Subscribe To Our Newsletter To Get The Latest Great Deals And Reviews</p>
  <div class="signup-field">Enter Email Address<span class="go">Go</span></div>
</section>

<footer class="sitefoot">
  <div class="fcol services" style="left:75px">
    <h4>All Services Reviewed</h4>
    <ul>
      <li>Annuities</li><li>Auto Insurance</li><li>Credit Monitoring</li><li>Credit Repair</li><li>Debt Management</li><li>Homeowners Insurance</li><li>Identity Theft</li><li>Life Insurance</li>
      <li>Mortgages</li><li>Online Brokerages</li><li>Payday Loans</li><li>Personal Finance</li><li>Student Loan Consolidation</li><li>Tax Settlement</li>
    </ul>
  </div>
  <div class="fcol" style="left:503px">
    <h4>Popular Services Reviewed</h4>
    <ul><li>Debt Management</li><li>Payday Loans</li><li>Credit Cards</li></ul>
  </div>
  <div class="fcol disclaim" style="left:790px">
    <h4>Advertising Disclosure:</h4>
    <p>CoinHarbor.com is an independent advertising supported comparison service. CoinHarbor.com may be compensated in exchange for featured placement of certain sponsored products and services, or your clicking on links posted on this website.</p>
    <div class="follow">
      <h4>Follow Us</h4>
      <div class="social"><a href="#">Friendhub</a><a href="#">Chirply</a><a href="#">Clipcast</a><a href="#">Circlenet</a><a href="#">Workmesh</a></div>
    </div>
  </div>
</footer>
<div class="bottombar">
  <span>Copyright © 2017 CoinHarbor. All rights reserved.</span>
  <span>About us / Privacy Policy / Terms of Service / Contact us</span>
</div>

</body>
</html>
```